Zelvo Stationary

Design the stationary of Zelvo Promotions Group.

Zelvo is a BTL company, BTL meaning "below the line". In other words Zelvo is a Promotional Marketing company (the company that design the brands promotional activities).

The design should transmit creativity, agility, boldness.

I need:
* Bis Card
* Letter head
* Envelopes, both vertical and horizontal (for legal size), and letter envelope
* Folders
* PPT template (Title page and regular page)
* CD slip (CD envelope)
* ID card (employee card)

And what ever else you want to throw in.
Updates

Guys,

Something I missed from the brief.   The predominat color should be RED.

Also, have fun and play with the exclamation mark (!) of the logo. 

Hi guys, more comments:

Remember that Zelvo is a "creativity" agency, not in the advertising side but on the promotional side, and that should reflect on the stationary.

 I want a bold design.  Bold and yet crisp.

 

Guys, i just uploaded the Logo in AI format.

I Also uploaded the actual Zelvo Bis Card, wich I like.  So I will like to see some designs with that bis card approach.

Guys, I am so sorry, but I notice in your last post that I upladed a wrong design ("13154_promotions_group_zelvo_brief225630.ai").  The problem was that I asked the designer the file in AI format and he send me thw wrong file, and since I dont have Illustrator I could not verify it.

The differences are minor, I just already ask him the correct one (similar to the EPS file).

Sorry                                   

Just post the correct AI file : "Zelvo Logo.ai"

Reason: I'm expecting more designs to choose from and also I wont be available tomorrow to decide.

Reason: Sorry guys, but we are not there yet!

Target Market(s)

Marketing directors, Marketing Managers

Industry/Entity Type

Legal

Requirements
Must have
• Must work with the logo attached.
The predominat color should be RED.
Play and have fun with the exclamation mark (!).
Should not have
• * No old fonts

Should not be:
* boring
* Informal
* rigid

```html
<!DOCTYPE html>
<html lang="en">
<head>
<meta charset="utf-8">
<title>Zelvo Promotions Group Stationery</title>
<link href="https://fonts.googleapis.com/css2?family=Open+Sans:wght@400;600;800&display=swap" rel="stylesheet">
<style>
:root{
  --red:#c8161d;
  --red-deep:#7c0a0f;
  --ink:#1d1d1d;
  --band:#222;
  --paper:#ffffff;
  --grey:#8a8a8a;
  --stage:#e4e4e4;
}
*{box-sizing:border-box;margin:0;padding:0}
html,body{width:1200px;height:589px;overflow:hidden}
body{background:var(--stage);font-family:"Open Sans",Arial,sans-serif;color:var(--ink);position:relative}
.piece{position:absolute;overflow:hidden;box-shadow:0 3px 10px rgba(0,0,0,.25)}
.red-face{background:radial-gradient(ellipse at 40% 35%,var(--red) 0%,#a81016 55%,var(--red-deep) 100%)}
.wordmark{display:flex;align-items:center;gap:5px;font-weight:800;letter-spacing:-.5px;line-height:1}
.wordmark .dot{border-radius:50%;background:var(--red);display:inline-block}
.on-red .wordmark{color:#fff}
.on-red .wordmark .dot{background:var(--ink)}
.band{position:absolute;left:0;right:0;background:var(--band);color:#ddd;font-size:7px;line-height:1.5;padding:6px 14px}
.band b{color:var(--red);font-weight:600}
.accent-circle{position:absolute;border-radius:50%;border:10px solid var(--ink);background:var(--red)}

/* letterhead */
.letterhead{left:40px;top:40px;width:290px;height:410px;background:var(--paper);padding:22px 24px}
.letterhead .wordmark{font-size:22px;color:var(--ink)}
.letterhead .wordmark .dot{width:8px;height:8px}
.letter-body{margin-top:34px;font-size:6.5px;line-height:1.6;color:#444;width:180px}
.letter-body p{margin-bottom:8px}
.letter-body ul{margin:0 0 8px 10px}
.letter-sign{font-size:6.5px;color:#444}
.letter-sign .name{margin-top:18px;font-weight:600}
.letterhead .band{bottom:0;background:#efefef;color:#555}

/* envelope */
.envelope{left:360px;top:40px;width:470px;height:240px}
.envelope .flap{position:absolute;left:0;top:0}
.envelope .wordmark{position:absolute;left:26px;top:90px;font-size:26px}
.envelope .wordmark .dot{width:9px;height:9px}
.envelope .band{bottom:26px;width:300px;padding-left:26px}
.envelope .accent-circle{width:90px;height:90px;right:38px;bottom:-28px}

/* business card */
.card-front{left:360px;top:305px;width:220px;height:125px;background:var(--paper);padding:18px}
.card-front .wordmark{font-size:22px;color:var(--ink)}
.card-front .wordmark .dot{width:8px;height:8px}
.card-tag{position:absolute;right:0;top:58px;background:var(--red);color:#fff;padding:5px 12px;font-size:7px;line-height:1.4}
.card-tag strong{font-weight:800;font-size:8px;display:block}
.card-front .contact{position:absolute;left:18px;bottom:12px;font-size:6px;line-height:1.5;color:#555}
.card-back{left:360px;top:448px;width:220px;height:125px}
.card-back .wordmark{position:absolute;left:18px;top:48px;font-size:24px}
.card-back .wordmark .dot{width:8px;height:8px}
.card-back .accent-circle{width:60px;height:60px;right:18px;bottom:-14px;border-width:7px}

/* cd sleeve */
.cd-sleeve{left:600px;top:300px;width:230px;height:230px}
.cd-sleeve .thumb{position:absolute;left:85px;top:-30px;width:60px;height:60px;border-radius:50%;background:var(--ink)}
.cd-sleeve .accent-circle{width:80px;height:80px;right:24px;top:70px}
.cd-sleeve .tagline{position:absolute;left:18px;bottom:52px;color:#fff;font-size:8px;font-weight:600;letter-spacing:1px}
.cd-sleeve .band{bottom:0;height:44px;padding:12px 18px}
.cd-sleeve .wordmark{font-size:20px}
.cd-sleeve .wordmark .dot{width:7px;height:7px}

/* folder */
.folder{left:850px;top:40px;width:310px;height:420px}
.folder .wordmark{position:absolute;left:26px;top:30px;font-size:30px}
.folder .wordmark .dot{width:10px;height:10px}
.folder .band{bottom:48px;padding-left:26px}
.folder .accent-circle{width:110px;height:110px;right:28px;bottom:80px;border-width:14px}
</style>
</head>
<body>

<section class="piece letterhead" aria-label="Letterhead">
  <div class="wordmark">zelvo<span class="dot"></span></div>
  <div class="letter-body">
    <p>Dear Mr. First Last</p>
    <p>Thank you for your interest in our promotional services. We look forward to working with you.</p>
    <p>Qualifications:</p>
    <ul><li>add stuff here</li><li>add stuff here</li><li>add stuff here</li></ul>
  </div>
  <div class="letter-sign">
    <p>Sincerely,</p>
    <p class="name">Dario Menlaw</p>
  </div>
  <div class="band">P.O. Box 1200 Harbor City 40210<br><b>T</b> +00 (2) 555 0148 &nbsp; <b>F</b> +00 (2) 555 0149 &nbsp; www.zelvopromo.com</div>
</section>

<section class="piece envelope red-face on-red" aria-label="Envelope">
  <svg class="flap" width="470" height="240" viewBox="0 0 470 240" aria-hidden="true">
    <polygon points="0,0 470,0 235,70" fill="#1d1d1d"/>
    <polygon points="0,0 235,70 470,0 470,6 235,78 0,6" fill="#000" opacity=".35"/>
  </svg>
  <div class="wordmark">zelvo<span class="dot"></span></div>
  <div class="band">P.O. Box 1200 Harbor City 40210<br><b>T</b> +00 (2) 555 0148 &nbsp; <b>F</b> +00 (2) 555 0149 &nbsp; www.zelvopromo.com</div>
  <div class="accent-circle"></div>
</section>

<section class="piece card-front" aria-label="Business card front">
  <div class="wordmark">zelvo<span class="dot"></span></div>
  <div class="card-tag"><strong>Dario Menlaw</strong>Account Director</div>
  <div class="contact">P.O. Box 1200 Harbor City 40210<br>+00 (2) 555 0148 &nbsp; www.zelvopromo.com</div>
</section>

<section class="piece card-back red-face on-red" aria-label="Business card back">
  <div class="wordmark">zelvo<span class="dot"></span></div>
  <div class="accent-circle"></div>
</section>

<section class="piece cd-sleeve red-face on-red" aria-label="CD sleeve">
  <div class="thumb"></div>
  <div class="accent-circle"></div>
  <p class="tagline">YOUR TAGLINE HERE</p>
  <div class="band"><div class="wordmark">zelvo<span class="dot"></span></div></div>
</section>

<section class="piece folder red-face on-red" aria-label="Presentation folder">
  <div class="wordmark">zelvo<span class="dot"></span></div>
  <div class="accent-circle"></div>
  <div class="band">P.O. Box 1200 Harbor City 40210<br><b>T</b> +00 (2) 555 0148 &nbsp; <b>F</b> +00 (2) 555 0149 &nbsp; www.zelvopromo.com</div>
</section>

</body>
</html>
```